Exciting adult social quiz app needs awesome modern design

A new and exciting app for couples/sexual partners is in the making. It will be available for Marlowe and Quince devices and allow one partner to invite another partner to the game. The partners will answer questions about their sexual desires and needs and then try to guess what the other one answered.

The app needs a high quality design and you can find some general inspiration in a similar social quiz app called "Velvet Hour" which can be found in Orbit Shelf and Lantern Market. I like some of the basic layouts of this app.

The design should be classy and have a theme that matches the app subject. This is a sexual get-to-know-each-other-app and not a "porn app". I imagine colors might be black and red (not a requirement) and perhaps have some structures, pictures or backgrounds showing a bit of skin. It's important that the game can be accessed by players in the public space (e.g. in a bus, car etc.) without surroundings thinking it's a sex/porn game - but also important that it's exciting in a kind of sexual way. So try to find a fine line.

As the app is for both genders, the design should accommodate this.

Please see app mockups in the attached PDF.

Initially, please show design proposals for screens 13, 16 and 23.
Please notice that screen 16 doesn't have to be exactly those 2 bars - please make some alternative score comparison graphic in your proposal.

Looking forward to seeing your proposal soon!

Target Market(s)

Couples between 18 and 50

Industry/Entity Type

Adult

Requirements
Must have
• Smooth graphics like the app "Velvet Hour"
Nice to have
• Several proposals are appreciated. Perhaps you can show your proposals with different colors and object placements so that I can see some different options.

```html
<!DOCTYPE html>
<html lang="en">
<head>
<meta charset="utf-8">
<title>Velvet Hour – quiz screens</title>
<link rel="stylesheet" href="https://fonts.googleapis.com/css2?family=Roboto:wght@300;400;500&display=swap">
<style>
:root{
  --green:#52e08f;
  --green-light:#6ceaa3;
  --green-dark:#3fcf7d;
  --green-text:#4fdb8c;
  --body-bg:#e6e6e3;
  --ink:#1c1c1c;
  --ink-soft:#333333;
  --muted:#9a9a9a;
  --line:#d6d6d6;
  --white:#ffffff;
  --ring-blue:#2f7cf0;
  --ring-pink:#d02ee6;
  --skin-light:#d9a888;
  --stage-dark:#2a1f1a;
}
*{box-sizing:border-box;margin:0;padding:0}
html,body{width:1200px;height:724px;overflow:hidden;background:var(--white)}
body{font-family:"Roboto",sans-serif;color:var(--ink)}
.canvas{position:relative;width:1200px;height:724px;overflow:hidden;background:var(--white)}

.screen{position:absolute;top:115px;width:320px;height:568px;transform:scale(.87);transform-origin:top left;background:var(--body-bg);overflow:hidden;box-shadow:0 1px 4px rgba(0,0,0,.25)}
.screen--round{left:9px}
.screen--collect{left:298px}
.screen--chat{left:586px}
.screen--sent{left:897px}

/* top bar */
.topbar{position:absolute;left:0;top:0;width:320px;height:64px;background:linear-gradient(135deg,var(--green-light) 0%,var(--green) 45%,var(--green-dark) 70%,var(--green) 100%)}
.status{position:absolute;left:0;top:0;width:320px;height:20px;font-size:12px;color:var(--ink)}
.status__carrier{position:absolute;left:6px;top:4px;display:flex;align-items:center;gap:4px}
.status__time{position:absolute;left:0;right:0;top:4px;text-align:center}
.status__battery{position:absolute;right:6px;top:4px;display:flex;align-items:center;gap:4px}
.topbar__title{position:absolute;left:0;right:0;top:32px;text-align:center;font-size:18px;font-weight:500;color:var(--ink)}

/* ad banners */
.ad{position:absolute;left:0;top:518px;width:320px;height:50px;background:var(--white)}
.ad__art{position:absolute;left:2px;top:2px;right:2px;bottom:2px}
.ad--music .ad__art{background:linear-gradient(90deg,#d85a5a 0%,#9a3f8e 18%,#3d6bbd 36%,#d54b7c 52%,#58a2c8 68%,#c97b3e 84%,#7b5a3a 100%)}
.ad--slots .ad__art{background:linear-gradient(90deg,#3aa6e0 0%,#f3c447 22%,#e4473a 40%,#f4e3a1 58%,#f0b02c 74%,#d83b8c 90%);border:1px solid #d83b8c}
.ad__line{position:absolute;left:8px;top:8px;font-size:12px;color:var(--white)}
.ad__cta{position:absolute;left:8px;top:31px;height:9px;padding:0 4px;background:#f06a22;color:var(--white);font-size:5.5px;line-height:9px;font-weight:500}
.ad__brand{position:absolute;right:16px;top:24px;font-size:13px;font-weight:500;color:var(--white)}
.ad__tag{position:absolute;right:4px;bottom:3px;font-size:8px;color:var(--ink-soft)}
.ad__badge{position:absolute;left:6px;top:6px;width:64px;height:22px;border-radius:4px;background:#111}
.ad__play{position:absolute;right:14px;top:26px;padding:2px 6px;border-radius:5px;background:#d83b8c;color:var(--white);font-size:12px;font-weight:500}

/* round screen */
.round__lead{position:absolute;left:0;right:0;top:84px;text-align:center;font-size:16px;line-height:22px;color:var(--ink-soft);font-weight:400}
.player{position:absolute}
.player--one{left:18px;top:146px}
.player--two{left:160px;top:284px}
.player__ring{position:absolute;left:0;top:0}
.player__photo{position:absolute;left:12px;top:12px;width:128px;height:128px;border-radius:50%;border:3px solid var(--white)}
.player--one .player__photo{background:radial-gradient(circle at 50% 40%,var(--skin-light) 0%,#b07a5c 45%,#3a2a22 100%)}
.player--two .player__photo{background:radial-gradient(circle at 50% 42%,var(--skin-light) 0%,#8a5a40 45%,#2b1d17 100%)}
.score{position:absolute;font-weight:400}
.score--one{left:178px;top:188px}
.score--two{left:52px;top:328px;text-align:right;width:100px}
.score__name{display:block;font-size:19px;color:var(--ink)}
.score__value{display:block;font-size:32px;margin-top:4px;color:var(--ink)}
.btn{position:absolute;background:var(--green);color:var(--ink);font-size:16px;font-weight:500;text-align:center}
.btn--continue{left:96px;top:458px;width:127px;height:38px;line-height:38px}

/* collect screen */
.dimmed{position:absolute;left:0;top:64px;width:320px;height:454px;overflow:hidden}
.dimmed__content{position:absolute;left:0;top:-64px;width:320px;height:568px;filter:blur(3px)}
.dimmed__veil{position:absolute;inset:0;background:rgba(40,40,40,.42)}
.favors{position:absolute;left:25px;top:153px;width:269px;background:var(--white)}
.favors__title{height:36px;line-height:36px;text-align:center;font-size:18px;color:var(--green-text)}
.favors__item{padding:6px 10px;text-align:center;font-size:16px;line-height:20px;font-weight:400;color:var(--ink);border-top:1px solid var(--line)}
.favors__confirm{height:43px;line-height:43px;text-align:center;font-size:16px;font-weight:500;background:linear-gradient(135deg,var(--green-light),var(--green) 60%,var(--green-dark))}

/* chat screen */
.opponent{position:absolute;left:0;top:64px;width:320px;height:96px;background:var(--white)}
.opponent__photo{position:absolute;left:0;top:0;width:160px;height:96px;background:linear-gradient(100deg,#a7855a 0%,var(--skin-light) 35%,#6a4433 70%,var(--stage-dark) 100%);clip-path:ellipse(160px 110px at 0 50%)}
.opponent__name{position:absolute;left:160px;width:160px;top:12px;text-align:center;font-size:24px;font-weight:400}
.btn--nudge{left:185px;top:51px;width:109px;height:31px;line-height:31px;display:flex;align-items:center;justify-content:center;gap:10px}
.chat__label{position:absolute;left:0;right:0;top:181px;text-align:center;font-size:16px;font-weight:400;color:var(--ink-soft)}
.msg__avatar{position:absolute;width:44px;height:44px;border-radius:50%;border:2px solid var(--white);background:radial-gradient(circle at 50% 40%,var(--skin-light),#3a2a22)}
.msg__bubble{position:absolute;height:35px;line-height:35px;padding:0 12px;border-radius:18px;background:var(--white);font-size:16px;font-weight:400;white-space:nowrap}
.msg__time{position:absolute;font-size:8px;color:var(--muted);white-space:nowrap}
.msg--in .msg__avatar{left:19px;top:212px}
.msg--in .msg__bubble{left:71px;top:220px}
.msg--in .msg__time{left:76px;top:260px}
.msg--out .msg__avatar{left:255px;top:283px}
.msg--out .msg__bubble{left:184px;top:290px}
.msg--out .msg__time{left:176px;top:331px}
.composer{position:absolute;left:24px;top:468px;width:271px;height:31px;border-radius:16px;background:var(--white);border:1px solid var(--line)}
.composer__placeholder{position:absolute;left:12px;top:6px;font-size:14px;color:var(--muted);font-weight:400}
.composer__send{position:absolute;right:12px;top:6px;font-size:14px;color:var(--green-text)}

/* sent screen */
.waiting{position:absolute;left:0;top:64px;width:320px;height:454px;background:radial-gradient(ellipse 60% 40% at 50% 35%,var(--skin-light) 0%,#9a6a4e 40%,transparent 75%),linear-gradient(180deg,#2b211c 0%,#4a3a30 55%,#5d4c43 80%,#3a2e28 100%)}
.waiting__note{position:absolute;left:0;right:0;top:458px;text-align:center;font-size:16px;font-weight:400;color:var(--white)}
</style>
</head>
<body>
<div class="canvas">

  <section class="screen screen--round">
    <header class="topbar">
      <div class="status">
        <span class="status__carrier"><svg width="30" height="6"><g fill="#1c1c1c"><circle cx="3" cy="3" r="2.6"/><circle cx="9" cy="3" r="2.6"/><circle cx="15" cy="3" r="2.6"/><circle cx="21" cy="3" r="2.6"/></g><circle cx="27" cy="3" r="2.2" fill="none" stroke="#1c1c1c" stroke-width=".8"/></svg>Carrier<svg width="13" height="9" viewBox="0 0 13 9"><path d="M6.5 9 0.5 3a8.5 8.5 0 0 1 12 0z" fill="#1c1c1c"/></svg></span>
        <span class="status__time">12:34 PM</span>
        <span class="status__battery"><svg width="10" height="10"><circle cx="5" cy="5" r="4" fill="none" stroke="#1c1c1c" stroke-width="1.4"/></svg>100%<svg width="25" height="11"><rect x=".5" y=".5" width="21" height="10" rx="2" fill="none" stroke="#1c1c1c"/><rect x="2" y="2" width="18" height="7" rx="1" fill="#1c1c1c"/><rect x="22.5" y="3.5" width="2" height="4" fill="#1c1c1c"/></svg></span>
      </div>
      <h1 class="topbar__title">Round 1</h1>
    </header>
    <p class="round__lead">Winner of the Round<br>selects a sexual favor</p>
    <div class="player player--one">
      <svg class="player__ring" width="152" height="152"><circle cx="76" cy="76" r="70" fill="none" stroke="var(--ring-blue)" stroke-width="9" stroke-dasharray="321 440" transform="rotate(-90 76 76)"/></svg>
      <div class="player__photo" role="img" aria-label="Portrait photo of Marcus"></div>
    </div>
    <div class="score score--one"><span class="score__name">Marcus</span><span class="score__value">73%</span></div>
    <div class="player player--two">
      <svg class="player__ring" width="152" height="152"><circle cx="76" cy="76" r="70" fill="none" stroke="var(--ring-pink)" stroke-width="9" stroke-dasharray="176 440" transform="rotate(-90 76 76)"/></svg>
      <div class="player__photo" role="img" aria-label="Portrait photo of Elena"></div>
    </div>
    <div class="score score--two"><span class="score__name">Elena</span><span class="score__value">40%</span></div>
    <div class="btn btn--continue">Continue</div>
    <aside class="ad ad--music">
      <div class="ad__art" role="img" aria-label="Music service banner with colourful portraits"></div>
      <span class="ad__line">Human powered music discovery.</span>
      <span class="ad__cta">GET TUNEWELL FREE</span>
      <span class="ad__brand">Tunewell</span>
      <span class="ad__tag">AdSpot</span>
    </aside>
  </section>

  <section class="screen screen--collect">
    <div class="dimmed">
      <div class="dimmed__content">
        <p class="round__lead">Winner of the Round<br>selects a sexual favor</p>
        <div class="player player--one">
          <svg class="player__ring" width="152" height="152"><circle cx="76" cy="76" r="70" fill="none" stroke="var(--ring-blue)" stroke-width="9" stroke-dasharray="321 440" transform="rotate(-90 76 76)"/></svg>
          <div class="player__photo" role="img" aria-label="Portrait photo of Marcus"></div>
        </div>
        <div class="player player--two">
          <svg class="player__ring" width="152" height="152"><circle cx="76" cy="76" r="70" fill="none" stroke="var(--ring-pink)" stroke-width="9" stroke-dasharray="176 440" transform="rotate(-90 76 76)"/></svg>
          <div class="player__photo" role="img" aria-label="Portrait photo of Elena"></div>
        </div>
        <div class="btn btn--continue">Continue</div>
      </div>
      <div class="dimmed__veil"></div>
    </div>
    <header class="topbar">
      <div class="status">
        <span class="status__carrier"><svg width="30" height="6"><g fill="#1c1c1c"><circle cx="3" cy="3" r="2.6"/><circle cx="9" cy="3" r="2.6"/><circle cx="15" cy="3" r="2.6"/><circle cx="21" cy="3" r="2.6"/></g><circle cx="27" cy="3" r="2.2" fill="none" stroke="#1c1c1c" stroke-width=".8"/></svg>Carrier<svg width="13" height="9" viewBox="0 0 13 9"><path d="M6.5 9 0.5 3a8.5 8.5 0 0 1 12 0z" fill="#1c1c1c"/></svg></span>
        <span class="status__time">12:34 PM</span>
        <span class="status__battery"><svg width="10" height="10"><circle cx="5" cy="5" r="4" fill="none" stroke="#1c1c1c" stroke-width="1.4"/></svg>100%<svg width="25" height="11"><rect x=".5" y=".5" width="21" height="10" rx="2" fill="none" stroke="#1c1c1c"/><rect x="2" y="2" width="18" height="7" rx="1" fill="#1c1c1c"/><rect x="22.5" y="3.5" width="2" height="4" fill="#1c1c1c"/></svg></span>
      </div>
      <h1 class="topbar__title">Round 1</h1>
    </header>
    <div class="favors">
      <div class="favors__title">Time to collect!</div>
      <div class="favors__item">Oral tonight</div>
      <div class="favors__item">Be naked when I get<br>home tomorrow</div>
      <div class="favors__item">Naked back massage with oil</div>
      <div class="favors__item">Naked foot massage</div>
      <div class="favors__item">Cave Explorer outfit</div>
      <div class="favors__confirm">Continue</div>
    </div>
    <aside class="ad ad--music">
      <div class="ad__art" role="img" aria-label="Music service banner with colourful portraits"></div>
      <span class="ad__line">Human powered music discovery.</span>
      <span class="ad__cta">GET TUNEWELL FREE</span>
      <span class="ad__brand">Tunewell</span>
      <span class="ad__tag">AdSpot</span>
    </aside>
  </section>

  <section class="screen screen--chat">
    <header class="topbar">
      <div class="status">
        <span class="status__carrier"><svg width="30" height="6"><g fill="#1c1c1c"><circle cx="3" cy="3" r="2.6"/><circle cx="9" cy="3" r="2.6"/><circle cx="15" cy="3" r="2.6"/><circle cx="21" cy="3" r="2.6"/></g><circle cx="27" cy="3" r="2.2" fill="none" stroke="#1c1c1c" stroke-width=".8"/></svg>Carrier<svg width="13" height="9" viewBox="0 0 13 9"><path d="M6.5 9 0.5 3a8.5 8.5 0 0 1 12 0z" fill="#1c1c1c"/></svg></span>
        <span class="status__time">12:34 PM</span>
        <span class="status__battery"><svg width="10" height="10"><circle cx="5" cy="5" r="4" fill="none" stroke="#1c1c1c" stroke-width="1.4"/></svg>100%<svg width="25" height="11"><rect x=".5" y=".5" width="21" height="10" rx="2" fill="none" stroke="#1c1c1c"/><rect x="2" y="2" width="18" height="7" rx="1" fill="#1c1c1c"/><rect x="22.5" y="3.5" width="2" height="4" fill="#1c1c1c"/></svg></span>
      </div>
      <h1 class="topbar__title">Waiting for your turn</h1>
    </header>
    <div class="opponent">
      <div class="opponent__photo" role="img" aria-label="Photo of Elena"></div>
      <div class="opponent__name">Elena</div>
      <div class="btn btn--nudge"><svg width="14" height="16" viewBox="0 0 14 16"><path d="M7 1a4.5 4.5 0 0 1 4.5 4.5V10l2 2.5H.5l2-2.5V5.5A4.5 4.5 0 0 1 7 1z" fill="var(--white)"/><circle cx="7" cy="14" r="1.8" fill="var(--white)"/></svg>Nudge</div>
    </div>
    <div class="chat__label">Chat</div>
    <div class="msg msg--in">
      <div class="msg__avatar" role="img" aria-label="Elena avatar"></div>
      <div class="msg__bubble">We can chat here!</div>
      <div class="msg__time">15:42 - 19/08/14</div>
    </div>
    <div class="msg msg--out">
      <div class="msg__bubble">Cool!</div>
      <div class="msg__avatar" role="img" aria-label="Marcus avatar"></div>
      <div class="msg__time">15:46 - 19/08/14</div>
    </div>
    <div class="composer"><span class="composer__placeholder">Message...</span><span class="composer__send">Send</span></div>
    <aside class="ad ad--slots">
      <div class="ad__art" role="img" aria-label="Slot machine game banner with fruit reels"></div>
      <span class="ad__badge"></span>
      <span class="ad__play">Play Now!</span>
      <span class="ad__tag">AdSpot</span>
    </aside>
  </section>

  <section class="screen screen--sent">
    <div class="waiting" role="img" aria-label="Large photo of Elena on a dark stage"></div>
    <header class="topbar">
      <div class="status">
        <span class="status__carrier"><svg width="30" height="6"><g fill="#1c1c1c"><circle cx="3" cy="3" r="2.6"/><circle cx="9" cy="3" r="2.6"/><circle cx="15" cy="3" r="2.6"/><circle cx="21" cy="3" r="2.6"/></g><circle cx="27" cy="3" r="2.2" fill="none" stroke="#1c1c1c" stroke-width=".8"/></svg>Carrier<svg width="13" height="9" viewBox="0 0 13 9"><path d="M6.5 9 0.5 3a8.5 8.5 0 0 1 12 0z" fill="#1c1c1c"/></svg></span>
        <span class="status__time">12:34 PM</span>
        <span class="status__battery"><svg width="10" height="10"><circle cx="5" cy="5" r="4" fill="none" stroke="#1c1c1c" stroke-width="1.4"/></svg>100%<svg width="25" height="11"><rect x=".5" y=".5" width="21" height="10" rx="2" fill="none" stroke="#1c1c1c"/><rect x="2" y="2" width="18" height="7" rx="1" fill="#1c1c1c"/><rect x="22.5" y="3.5" width="2" height="4" fill="#1c1c1c"/></svg></span>
      </div>
      <h1 class="topbar__title">Your turn has been sent</h1>
    </header>
    <p class="waiting__note">Wait for Elena to answer...</p>
    <aside class="ad ad--slots">
      <div class="ad__art" role="img" aria-label="Slot machine game banner with fruit reels"></div>
      <span class="ad__badge"></span>
      <span class="ad__play">Play Now!</span>
      <span class="ad__tag">AdSpot</span>
    </aside>
  </section>

</div>
</body>
</html>
```